Fun and Flexible Word Template Design for Classroom Learning Resources

We're a global arts and education nonprofit based in New York. We're looking for a 2-page Word template design for our new collection of Learning Resources.
Page 1 of the template should include:
1. Lanternbridge 9 logo (attached)
2. Resource title
3. Author photo
4. Author bio
5. Resource text
6. Sub-title text
7. Colored call-out box
Page 2 of the template should include:
2. Resource Title (in a smaller font)
3. Resource text
4. Sub-title text
5. Colored call-out box
The design must also adhere to our current brand guidelines: https://stylekit.example/lanternbridge-9
We've attached a very basic mock-up that includes the elements listed above. However, we encourage you to be more playful and/or creative with your design.
Our goal is to create a template that is flexible enough to accomodate a variety of resources (samples of 3 different resources are attached), that is also visually appealing enough to attract and hold the attention of busy educators.
Target Market(s)
Educators - Middle School, High School & College
Look and feel

```html
<!DOCTYPE html>
<html lang="en">
<head>
<meta charset="utf-8">
<title>Lanternbridge 9 – Learning Resource Template</title>
<link rel="stylesheet" href="https://fonts.googleapis.com/css2?family=Archivo:wght@500;700&family=Arimo:wght@400&family=Tinos:wght@400&display=swap">
<style>
  :root {
    --purple: #673293;
    --yellow: #e6cb45;
    --cream: #f1e6c8;
    --paper: #f3f5f6;
    --ink: #5e5e5e;
    --ink-dark: #222222;
    --stage: #2b2b2d;
    --white: #ffffff;
  }
  * { box-sizing: border-box; margin: 0; padding: 0; }
  html, body {
    width: 1200px; height: 887px; overflow: hidden;
    background: var(--stage);
  }
  .canvas { position: relative; width: 1200px; height: 887px; }
  .page {
    position: absolute; top: 118px; width: 460px; height: 651px;
    background: var(--paper); overflow: hidden;
  }
  .page--one { left: 114px; }
  .page--two { left: 627px; }
  .decor { position: absolute; inset: 0; width: 460px; height: 651px; }

  .brand { position: absolute; display: flex; align-items: center; gap: 6px; }
  .brand__mark { width: 12px; height: 12px; background: var(--purple); }
  .brand__name {
    font-family: 'Archivo', sans-serif; font-weight: 500; font-size: 13px;
    letter-spacing: 0; color: var(--purple);
  }
  .page--one .brand { left: 178px; top: 29px; }
  .page--two .brand { left: 186px; top: 27px; }

  .band { position: absolute; left: 0; top: 17px; width: 175px; height: 37px; background: var(--purple); }

  .title {
    position: absolute; left: 77px; top: 64px;
    font-family: 'Archivo', sans-serif; font-weight: 700; font-size: 30px;
    letter-spacing: 1px; color: var(--purple); line-height: 36px;
  }

  .author-block { position: absolute; left: 0; top: 127px; width: 140px; height: 192px; background: var(--purple); }
  .author-ring {
    position: absolute; left: 53px; top: 137px; width: 172px; height: 172px;
    border-radius: 50%; background: var(--paper);
  }
  .author-photo {
    position: absolute; left: 67px; top: 151px; width: 144px; height: 144px;
    border-radius: 50%;
    background: radial-gradient(circle at 50% 40%, #9a9a9a 0%, #5c5c5c 55%, #2e2e2e 100%);
  }

  .bio { position: absolute; left: 230px; top: 124px; width: 206px; }
  .bio__heading {
    font-family: 'Tinos', serif; font-weight: 400; font-size: 15px; color: var(--purple);
    margin-left: 2px; margin-bottom: 3px;
  }
  .bio__text {
    font-family: 'Tinos', serif; font-size: 8.4px; line-height: 9.75px;
    color: var(--ink); text-align: justify; hyphens: auto;
  }
  .bio__text + .bio__text { margin-top: 9.75px; }

  .section { position: absolute; left: 27px; width: 407px; }
  .section__heading {
    font-family: 'Archivo', sans-serif; font-weight: 700; font-size: 12.3px;
    color: var(--purple); line-height: 14px;
  }
  .section__heading--large { font-size: 21px; line-height: 24px; }
  .body-text {
    font-family: 'Arimo', sans-serif; font-size: 7.35px; line-height: 9.3px;
    color: var(--ink); text-align: justify; hyphens: auto;
  }
  .body-text + .body-text { margin-top: 9.3px; }

  .callout-heading {
    position: absolute; left: 27px; top: 518px;
    font-family: 'Archivo', sans-serif; font-weight: 700; font-size: 12.3px; color: var(--purple);
  }
  .callout {
    position: absolute; left: 27px; top: 541px; width: 405px; height: 87px;
    background: var(--yellow); box-shadow: 0 0 0 4px var(--white);
    padding: 7px 5px;
  }
  .callout p {
    font-family: 'Arimo', sans-serif; font-size: 7.35px; line-height: 9.3px; color: var(--ink-dark);
  }
  .callout p + p { margin-top: 9.3px; }
</style>
</head>
<body>
<main class="canvas">

  <section class="page page--one">
    <svg class="decor" viewBox="0 0 460 651" aria-hidden="true">
      <circle cx="47" cy="31" r="14" fill="var(--cream)"/>
      <circle cx="419" cy="404" r="24" fill="var(--cream)" opacity="0.7"/>
      <circle cx="466" cy="63" r="43" fill="none" stroke="var(--cream)" stroke-width="1.2"/>
      <circle cx="466" cy="63" r="54" fill="none" stroke="var(--purple)" stroke-width="2"/>
      <g fill="var(--purple)">
        <circle cx="404" cy="3" r="6"/>
        <circle cx="407" cy="16" r="6"/>
        <circle cx="419" cy="28" r="6"/>
        <circle cx="436" cy="37" r="6"/>
        <circle cx="453" cy="36" r="6"/>
      </g>
      <path d="M362 651 V570 Q362 549 383 549 H460 V651 Z" fill="var(--purple)"/>
    </svg>

    <div class="brand"><span class="brand__mark"></span><span class="brand__name">Lanternbridge 9</span></div>
    <h1 class="title">LOREMIPSUMDOLOR</h1>

    <div class="author-block"></div>
    <div class="author-ring"></div>
    <div class="author-photo" role="img" aria-label="Black-and-white portrait of the author holding an accordion"></div>
    <svg class="decor" viewBox="0 0 460 651" aria-hidden="true">
      <g fill="var(--yellow)">
        <circle cx="206" cy="280" r="2.4" transform="rotate(-70 190 280)"/>
        <circle cx="206" cy="280" r="2.4" transform="rotate(-40 190 280)"/>
        <circle cx="206" cy="280" r="2.4" transform="rotate(-10 190 280)"/>
        <circle cx="206" cy="280" r="2.4" transform="rotate(20 190 280)"/>
        <circle cx="206" cy="280" r="2.4" transform="rotate(50 190 280)"/>
        <circle cx="206" cy="280" r="2.4" transform="rotate(80 190 280)"/>
        <circle cx="206" cy="280" r="2.4" transform="rotate(110 190 280)"/>
        <circle cx="206" cy="280" r="2.4" transform="rotate(140 190 280)"/>
        <circle cx="206" cy="280" r="2.4" transform="rotate(170 190 280)"/>
        <circle cx="206" cy="280" r="2.4" transform="rotate(200 190 280)"/>
      </g>
    </svg>

    <div class="bio">
      <h2 class="bio__heading">About Bio</h2>
      <p class="bio__text">Lorem ipsum dolor sit amet, consectetuer adipiscing elit, sed diam nonummy nibh euismod tincidunt ut laoreet dolore magna aliquam erat volutpat. Ut wisi enim ad minim veniam, quis nostrud exerci tation ullamcorper suscipit lobortis nisl ut aliquip ex ea commodo consequat. Duis autem vel eum iriure dolor in hendrerit in vulputate velit esse molestie consequat, vel illum dolore eu feugiat nulla facilisis at vero eros et accumsan et iusto odio dignissim qui blandit praesent luptatum zzril delenit augue duis dolore te feugait nulla facilisi.</p>
      <p class="bio__text">Lorem ipsum dolor sit amet, cons ectetuer adipiscing elit, sed diam nonummy nibh euismod tincidunt ut laoreet dolore magna aliquam erat volutpat. Ut wisi enim ad minim veniam, quis nostrud exerci tation ullamcorper suscipit lobortis nisl ut aliquip magna aliquam erat volutpat. Ut wisi enim ad minim veniam, quis nostrud exerci tation ullamcorper suscipit lobortis nisl ut aliquip</p>
    </div>

    <div class="section" style="top:348px">
      <h2 class="section__heading">ResourceText</h2>
      <p class="body-text">Lorem ipsum dolor sit amet, consectetuer adipiscing elit, sed diam nonummy nibh euismod tincidunt ut laoreet dolore magna aliquam erat volutpat. Ut wisi enim ad minim veniam, quis nostrud exerci tation ullamcorper suscipit lobortis nisl ut aliquip ex ea commodo consequat. Duis autem vel eum iriure dolor in hendrerit in vulputate velit esse molestie consequat, vel illum dolore eu feugiat nulla facilisis at vero eros et accumsan et iusto odio dignissim qui blandit praesent luptatum zzril delenit augue duis dolore te feugait nulla facilisi.</p>
    </div>

    <div class="section" style="top:431px">
      <h2 class="section__heading">Sub-title text</h2>
      <p class="body-text">Lorem ipsum dolor sit amet, consectetuer adipiscing elit, sed diam nonummy nibh euismod tincidunt ut laoreet dolore magna aliquam erat volutpat. Ut wisi enim ad minim veniam, quis nostrud exerci tation ullamcorper suscipit lobortis nisl ut aliquip ex ea commodo consequat. Duis autem vel eum iriure dolor in hendrerit in vulputate velit esse molestie consequat, vel illum dolore eu feugiat nulla facilisis at vero eros et accumsan et iusto odio dignissim qui blandit praesent luptatum zzril delenit augue duis dolore te feugait nulla facilisi.</p>
    </div>

    <h2 class="callout-heading">ColoredCall-outtext–boxed</h2>
    <div class="callout">
      <p>Lorem ipsum dolor sit amet, consectetuer adipiscing elit, sed diam nonummy nibh euismod tincidunt ut laoreet dolore magna aliquam erat volutpat. Ut wisi enim ad minim veniam, quis nostrud exerci tation ullamcorper suscipit lobortis nisl ut aliquip ex ea commodo consequat. Duis autem vel eum iriure dolor in hendrerit in vulputate velit esse molestie consequat.</p>
      <p>vel illum dolore eu feugiat nulla facilisis at vero eros et accumsan et iusto odio dignissim qui blandit praesent luptatum zzril delenit augue duis dolore te feugait nulla facilisi.</p>
    </div>
  </section>

  <section class="page page--two">
    <svg class="decor" viewBox="0 0 460 651" aria-hidden="true">
      <circle cx="412" cy="27" r="16" fill="var(--cream)"/>
      <circle cx="39" cy="405" r="21" fill="var(--cream)" opacity="0.7"/>
      <circle cx="436" cy="350" r="5" fill="var(--cream)"/>
      <circle cx="466" cy="63" r="54" fill="none" stroke="var(--purple)" stroke-width="2"/>
      <g fill="var(--purple)">
        <circle cx="404" cy="3" r="6"/>
        <circle cx="407" cy="16" r="6"/>
        <circle cx="419" cy="28" r="6"/>
        <circle cx="436" cy="37" r="6"/>
        <circle cx="453" cy="36" r="6"/>
      </g>
      <path d="M0 651 V549 H84 Q104 549 104 569 V651 Z" fill="var(--purple)"/>
      <path d="M332 651 V565 Q340 517 410 517 H460 V651 Z" fill="var(--purple)"/>
    </svg>

    <div class="band"></div>
    <div class="brand"><span class="brand__mark"></span><span class="brand__name">Lanternbridge 9</span></div>

    <div class="section" style="top:65px">
      <h2 class="section__heading section__heading--large">ResourceText</h2>
      <p class="body-text">Lorem ipsum dolor sit amet, consectetuer adipiscing elit, sed diam nonummy nibh euismod tincidunt ut laoreet dolore magna aliquam erat volutpat. Ut wisi enim ad minim veniam, quis nostrud exerci tation ullamcorper suscipit lobortis nisl ut aliquip ex ea commodo consequat. Duis autem vel eum iriure dolor in hendrerit in vulputate velit esse molestie consequat, vel illum dolore eu feugiat nulla facilisis at vero eros et accumsan et iusto odio dignissim qui blandit praesent luptatum zzril delenit augue duis dolore te feugait nulla facilisi. Lorem ipsum dolor sit amet, cons ectetuer adipiscing elit, sed diam nonummy nibh euismod tincidunt ut laoreet dolore magna aliquam erat volutpat. Ut wisi enim ad minim veniam, quis nostrud exerci tation ullamcorper suscipit lobortis nisl ut aliquip ex ea commodo consequat. Lorem ipsum dolor sit amet, consectetuer adipiscing elit, sed diam nonummy nibh euismod tincidunt ut laoreet dolore magna aliquam erat volutpat. Ut wisi enim ad minim veniam, quis nostrud exerci tation ullamcorper suscipit lobortis nisl ut aliquip ex ea commodo consequat. Duis autem vel eum iriure dolor in hendrerit in vulputate velit esse molestie consequat, vel illum dolore eu feugiat nulla facilisis at vero eros et accumsan et iusto odio dignissim qui blandit praesent luptatum zzril delenit augue duis dolore te feugait nulla facilisi. Lorem ipsum dolor sit amet, cons ectetuer adipiscing elit, sed diam nonummy nibh euismod tincidunt ut laoreet dolore magna aliquam erat volutpat.</p>
      <p class="body-text">Lorem ipsum dolor sit amet, consectetuer adipiscing elit, sed diam nonummy nibh euismod tincidunt ut laoreet dolore magna aliquam erat volutpat. Ut wisi enim ad minim veniam, quis nostrud exerci tation ullamcorper suscipit lobortis nisl ut aliquip ex ea commodo consequat. Duis autem vel eum iriure dolor in hendrerit in vulputate velit esse molestie consequat, vel illum dolore eu feugiat nulla facilisis at vero eros et accumsan et iusto odio dignissim qui blandit praesent luptatum zzril delenit augue duis dolore te feugait nulla facilisi.</p>
      <p class="body-text">Lorem ipsum dolor sit amet, cons ectetuer adipiscing elit, sed diam nonummy nibh euismod tincidunt ut laoreet dolore magna aliquam erat volutpat. Ut wisi enim ad minim veniam, quis nostrud exerci tation ullamcorper suscipit lobortis nisl ut aliquip ex ea commodo consequat.</p>
    </div>

    <div class="section" style="top:339px">
      <h2 class="section__heading section__heading--large">Sub-title text</h2>
      <p class="body-text">Lorem ipsum dolor sit amet, consectetuer adipiscing elit, sed diam nonummy nibh euismod tincidunt ut laoreet dolore magna aliquam erat volutpat. Ut wisi enim ad minim veniam, quis nostrud exerci tation ullamcorper suscipit lobortis nisl ut aliquip ex ea commodo consequat. Duis autem vel eum iriure dolor in hendrerit in vulputate velit esse molestie consequat, vel illum dolore eu feugiat nulla facilisis at vero eros et accumsan et iusto odio dignissim qui blandit praesent luptatum zzril delenit augue duis dolore te feugait nulla facilisi. Lorem ipsum dolor sit amet, cons ectetuer adipiscing elit, sed diam nonummy nibh euismod tincidunt ut laoreet dolore magna aliquam erat volutpat. Ut wisi enim ad minim veniam, quis nostrud exerci tation ullamcorper suscipit lobortis nisl ut aliquip ex ea commodo consequat. Lorem ipsum dolor sit amet, consectetuer adipiscing elit, sed diam nonummy nibh euismod tincidunt ut laoreet dolore magna aliquam erat volutpat. Ut wisi enim ad minim veniam, quis nostrud exerci tation ullamcorper suscipit lobortis nisl ut aliquip ex ea commodo consequat. Duis autem vel eum iriure dolor in hendrerit in vulputate velit esse molestie consequat, vel illum dolore eu feugiat nulla facilisis at vero eros et accumsan et iusto odio dignissim qui blandit praesent luptatum zzril delenit augue duis dolore te feugait nulla facilisi. Lorem ipsum dolor sit amet, cons ectetuer adipiscing elit, sed diam nonummy nibh euismod tincidunt ut laoreet dolore magna aliquam erat volutpat.</p>
    </div>

    <h2 class="callout-heading">ColoredCall-outtext–boxed</h2>
    <div class="callout">
      <p>Lorem ipsum dolor sit amet, consectetuer adipiscing elit, sed diam nonummy nibh euismod tincidunt ut laoreet dolore magna aliquam erat volutpat. Ut wisi enim ad minim veniam, quis nostrud exerci tation ullamcorper suscipit lobortis nisl ut aliquip ex ea commodo consequat. Duis autem vel eum iriure dolor in hendrerit in vulputate velit esse molestie consequat.</p>
      <p>vel illum dolore eu feugiat nulla facilisis at vero eros et accumsan et iusto odio dignissim qui blandit praesent luptatum zzril delenit augue duis dolore te feugait nulla facilisi.</p>
    </div>
  </section>

</main>
</body>
</html>
```